Business Cards Design for the electrical wholesaler: clean bold dynamic :)

We need a business card design that would follow our latest brand guidelines. As an electrical wholesaler we want to bring a fresh look and feel into the industry. The design should be clean bold and dynamic. It should come alive with the renewed energy of our green colour. Our grey colour should keep things balanced and complement the notion of maturity and responsibility. We employ Lato as a corporate font however are not bound by this font and we’re open to interpretation here.

Target Market(s)

Electrical contractors

Industry/Entity Type

Business

Contact Information for Business Card

Logo
Name & Surname: Halyna Dorosh
Job Title: Director of Marketing
Email: halya.dorosh@quillmail.example
Cell phone: XXX.XXX.XXXX
Address: 20517 - 87 Ave. Edmonton, AB, Canada. T6K 4N8
Business Phone: 780.555.0184
Website: www.brovix.example

Font styles to use
Other font styles liked:
• Lato

Requirements
Must have
• Logo & website
Nice to have
• Brand elements - some of them you may find in the attached Brand Guidelines (e.g. three lines on the background signifying "W")

```html
<!DOCTYPE html>
<html lang="en">
<head>
<meta charset="utf-8">
<title>Brovix Business Cards</title>
<link href="https://fonts.googleapis.com/css2?family=Work+Sans:wght@400;500;600&display=swap" rel="stylesheet">
<style>
  :root {
    --backdrop: #141414;
    --card-dark: #1c1c1c;
    --card-light: #353535;
    --brand-green: #8dc63f;
    --text-white: #f2f2f2;
  }
  * { margin: 0; padding: 0; box-sizing: border-box; }
  html, body { width: 1200px; height: 900px; overflow: hidden; background: var(--backdrop); }
  body { font-family: "Work Sans", sans-serif; color: var(--text-white); position: relative; }

  .card {
    position: absolute;
    left: 250px;
    width: 700px;
    height: 400px;
    background: linear-gradient(115deg, var(--card-dark) 0%, var(--card-dark) 45%, var(--card-light) 100%);
    box-shadow: 0 12px 30px rgba(0,0,0,0.6);
  }
  .card-front { top: 40px; }
  .card-back { top: 470px; }

  .wordmark { display: flex; align-items: center; gap: 14px; }
  .wordmark-square { width: 34px; height: 34px; background: var(--brand-green); }
  .wordmark-name { font-weight: 500; color: var(--text-white); letter-spacing: 1px; line-height: 1; }

  .card-front .wordmark { position: absolute; left: 50%; top: 50%; transform: translate(-50%, -50%); }
  .card-front .wordmark-name { font-size: 78px; }
  .card-front .wordmark-square { width: 46px; height: 46px; }

  .card-back .wordmark { position: absolute; left: 48px; top: 168px; }
  .card-back .wordmark-name { font-size: 56px; }

  .divider { position: absolute; left: 330px; top: 95px; width: 2px; height: 210px; background: var(--brand-green); }

  .contact { position: absolute; left: 368px; top: 100px; }
  .contact-name { font-size: 32px; font-weight: 600; color: var(--brand-green); line-height: 1.1; }
  .contact-title { font-size: 19px; font-weight: 400; margin-bottom: 18px; }
  .contact-address { font-size: 18px; line-height: 1.3; margin-bottom: 12px; letter-spacing: 0.5px; }
  .contact-line { display: flex; align-items: center; gap: 12px; font-size: 18px; line-height: 1.4; letter-spacing: 0.5px; }
  .contact-line svg { width: 14px; height: 14px; flex: none; }
</style>
</head>
<body>
  <section class="card card-front">
    <div class="wordmark">
      <span class="wordmark-square"></span>
      <span class="wordmark-name">brovix</span>
    </div>
  </section>

  <section class="card card-back">
    <div class="wordmark">
      <span class="wordmark-square"></span>
      <span class="wordmark-name">brovix</span>
    </div>

    <div class="divider"></div>

    <div class="contact">
      <p class="contact-name">Halyna Dorosh</p>
      <p class="contact-title">Founder</p>
      <p class="contact-address">20517 87ave<br>T6K4N8 Edmonton, Alberta</p>
      <p class="contact-line">
        <svg viewBox="0 0 14 14" aria-hidden="true"><path d="M3 1 L5 1 L6 4 L4.5 5.2 Q6 8.5 8.8 9.5 L10 8 L13 9 L13 11 Q12.5 13 10.5 13 Q2 11.5 1 3.5 Q1 1.5 3 1 Z" fill="var(--brand-green)"/></svg>
        780.555.0184
      </p>
      <p class="contact-line">
        <svg viewBox="0 0 14 14" aria-hidden="true"><rect x="1" y="3" width="12" height="8" fill="none" stroke="var(--brand-green)" stroke-width="1.4"/><path d="M1 3 L7 8 L13 3" fill="none" stroke="var(--brand-green)" stroke-width="1.4"/></svg>
        halya.dorosh@quillmail.example
      </p>
      <p class="contact-line">
        <svg viewBox="0 0 14 14" aria-hidden="true"><circle cx="7" cy="7" r="5.5" fill="none" stroke="var(--brand-green)" stroke-width="1.3"/><ellipse cx="7" cy="7" rx="2.4" ry="5.5" fill="none" stroke="var(--brand-green)" stroke-width="1.1"/><path d="M1.5 7 H12.5" stroke="var(--brand-green)" stroke-width="1.1"/></svg>
        www.brovix.example
      </p>
    </div>
  </section>
</body>
</html>
```